Wavelink Earphone Packaging Design

We want to use the packaging for 4-5 of our Wavelink Earphone series (Picture enclosed) and hence we would not like to put any product pictures on the packaging.

Material: E-Flute Paper box
Type: Window Box style
Design features we prefer: Colorful, creative, trendy, High tech.
Requirement: AI file is preferred
Size of Packaging: (L) 95 x (W) 40 x (H) 120 mm

Enclosed are a detailed description along with competitor designs for your reference.

Any further questions, please feel free to ask

```html
<!DOCTYPE html>
<html lang="en">
<head>
<meta charset="utf-8">
<title>Wavelink Earphone 5.0 – Packaging Panels</title>
<link rel="stylesheet" href="https://fonts.googleapis.com/css2?family=Raleway:wght@200;300;400;600;700&display=swap">
<style>
  :root {
    --stage: #7d7d7d;
    --violet: #7a3f9e;
    --indigo: #3f3f96;
    --teal: #2fb3b0;
    --ocean: #23689a;
    --navy: #2c4c8e;
    --magenta: #d93a97;
    --ink-light: #ffffff;
    --ink-soft: rgba(255, 255, 255, 0.55);
    --ink-faint: rgba(255, 255, 255, 0.28);
  }
  * { box-sizing: border-box; margin: 0; padding: 0; }
  html, body {
    width: 1200px;
    height: 1148px;
    overflow: hidden;
    background: var(--stage);
    font-family: "Raleway", sans-serif;
  }
  .dieline {
    position: absolute;
    left: 94px;
    top: 124px;
    display: flex;
    height: 900px;
  }
  .panel {
    position: relative;
    height: 100%;
    overflow: hidden;
    color: var(--ink-light);
  }
  .panel--side {
    width: 300px;
    background:
      radial-gradient(ellipse 60% 28% at 0% 47%, rgba(47, 179, 176, 0.85), transparent 70%),
      linear-gradient(180deg, var(--violet) 0%, var(--indigo) 28%, var(--ocean) 55%, var(--teal) 66%, var(--ocean) 80%, var(--navy) 100%);
  }
  .panel--back {
    width: 712px;
    background:
      radial-gradient(ellipse 38% 22% at 100% 38%, rgba(47, 179, 176, 0.9), transparent 72%),
      radial-gradient(ellipse 50% 30% at 20% 72%, rgba(47, 150, 180, 0.45), transparent 75%),
      linear-gradient(180deg, var(--violet) 0%, #5a3f9e 22%, var(--indigo) 45%, #2f5a9c 70%, var(--navy) 100%);
    border-left: 1px solid rgba(0, 0, 0, 0.12);
  }
  .side-title {
    position: absolute;
    top: 140px;
    left: 70px;
    writing-mode: vertical-rl;
    font-weight: 600;
    font-size: 74px;
    line-height: 1.0;
    letter-spacing: 0.5px;
    white-space: nowrap;
  }
  .side-version {
    position: absolute;
    top: 575px;
    left: 78px;
    writing-mode: vertical-rl;
    font-weight: 200;
    font-size: 178px;
    line-height: 1;
  }
  .thumb-notch {
    position: absolute;
    top: -100px;
    left: 470px;
    width: 170px;
    height: 170px;
    border-radius: 50%;
    background: var(--magenta);
  }
  .spec {
    position: absolute;
    top: 116px;
    left: 48px;
    font-size: 15px;
    line-height: 1.55;
    color: var(--ink-soft);
    font-weight: 300;
    list-style: none;
  }
  .spec__title {
    color: var(--ink-light);
    font-weight: 600;
    font-size: 16px;
    margin-bottom: 2px;
  }
  .window {
    position: absolute;
    top: 420px;
    left: 48px;
    width: 340px;
    height: 210px;
    border: 2px solid rgba(255, 255, 255, 0.75);
  }
  .window__label {
    position: absolute;
    top: 30px;
    left: 10px;
    width: 90px;
    height: 60px;
    background: #f2f2f2;
  }
  .product-note {
    position: absolute;
    top: 658px;
    left: 48px;
    width: 470px;
  }
  .product-note__name {
    font-size: 13px;
    font-weight: 600;
    font-style: italic;
    margin-bottom: 6px;
  }
  .product-note__body {
    font-size: 11px;
    line-height: 1.6;
    color: var(--ink-faint);
  }
  .marks {
    position: absolute;
    top: 790px;
    left: 48px;
  }
</style>
</head>
<body>
  <main class="dieline">
    <section class="panel panel--side">
      <h1 class="side-title">Wavelink<br>Earphone</h1>
      <p class="side-version">5.0</p>
    </section>

    <section class="panel panel--back">
      <div class="thumb-notch"></div>

      <ul class="spec">
        <li class="spec__title">Specification:</li>
        <li>Wavelink Version: 5.0</li>
        <li>Wireless Playback Duration: 3-4 h</li>
        <li>Standby Time: 60 h</li>
        <li>Wireless Range: 10 m</li>
        <li>Impedance: 32 Ω</li>
        <li>Sound Pressure Level: 100dB ± 3dB</li>
        <li>Frequency Response: 20-20kHz</li>
        <li>Driver Unit: 10mm</li>
      </ul>

      <div class="window">
        <div class="window__label"></div>
      </div>

      <div class="product-note">
        <p class="product-note__name">Wavelink Earphone 5.0</p>
        <p class="product-note__body">Wireless stereo earphones with clear sound, stable pairing and long battery life. Lightweight fit for daily use, travel and workouts. Charge fully before first use and keep away from water and heat.</p>
      </div>

      <svg class="marks" width="260" height="48" viewBox="0 0 260 48" role="img" aria-label="Certification marks">
        <g fill="none" stroke="#ffffff" stroke-width="3">
          <circle cx="22" cy="24" r="18"/>
          <circle cx="70" cy="24" r="18"/>
          <rect x="100" y="6" width="36" height="36" rx="4"/>
          <circle cx="166" cy="24" r="18"/>
          <circle cx="214" cy="24" r="18"/>
        </g>
      </svg>
    </section>
  </main>
</body>
</html>
```